A5, portrait
Theme is science
audience is VIPS, politicians, executives
this is a really important event, we want a very classy invitation
include logo for bloom and grow and lantern but lantern one bigger
images attached
Have attached some styles we like but doesn't need to be these colours. If we can incorporate some colours from our logo would be good but don't make too colourful and childish

You’re invited to the official opening and launch of Lantern, Centre of Discovery. an industry first, pioneering, STEM hub.

Saturday 30th April, 2022

10:00 am – 12:00 pm

42 Harlow Lane, Fernwood

Light canapes provided. Dress code is smart/casual

All guests will be given a guided walk through of Australia’s first dedicated STEM education hub for children aged 3-6.

Invitation only

RSVP: 18 April to marketing@bloomandgrow.edu.au

```html
<!DOCTYPE html>
<html lang="en">
<head>
<meta charset="utf-8">
<title>Lantern Opening Invitation</title>
<link rel="stylesheet" href="https://fonts.googleapis.com/css2?family=Crimson+Text:ital,wght@0,400;0,600;1,400&family=Montserrat:wght@800&display=swap">
<style>
  :root {
    --page-bg: #f2f1ef;
    --card-bg: #fffdfd;
    --ink: #333333;
    --heading: #2f3a4a;
    --red: #e03c36;
    --green: #7dbe3f;
    --blue: #1fa6df;
    --gold-line: #e6d3ad;
    --wash: rgba(240, 200, 215, 0.35);
  }
  * { margin: 0; padding: 0; box-sizing: border-box; }
  html, body { width: 800px; height: 1200px; overflow: hidden; background: var(--page-bg); }
  .invitation-card {
    position: absolute; left: 20px; top: 62px; width: 760px; height: 1076px;
    background: radial-gradient(ellipse 300px 260px at 540px 640px, var(--wash), transparent 70%), var(--card-bg);
    box-shadow: 0 4px 14px rgba(0,0,0,0.12);
    overflow: hidden;
    font-family: "Crimson Text", Georgia, serif;
    color: var(--ink);
    text-align: center;
  }
  .gold-frame {
    position: absolute; left: 44px; top: 65px; width: 695px; height: 959px;
    border: 1px solid var(--gold-line);
  }
  .floral-top-right {
    position: absolute; left: 500px; top: 0; width: 260px; height: 477px;
    border-radius: 0 0 0 70%;
    background: radial-gradient(circle at 75% 12%, rgba(201,56,90,0.75), transparent 32%),
                radial-gradient(circle at 80% 38%, rgba(179,164,220,0.7), transparent 30%),
                radial-gradient(circle at 78% 58%, rgba(236,128,170,0.7), transparent 28%),
                linear-gradient(200deg, rgba(143,176,138,0.55), rgba(143,176,138,0) 80%);
  }
  .floral-bottom-left {
    position: absolute; left: 0; top: 729px; width: 397px; height: 347px;
    border-radius: 0 70% 0 0;
    background: radial-gradient(circle at 45% 75%, rgba(179,164,220,0.75), transparent 35%),
                radial-gradient(circle at 15% 60%, rgba(220,205,235,0.8), transparent 35%),
                linear-gradient(20deg, rgba(143,176,138,0.5), rgba(143,176,138,0) 75%);
  }
  .brand-lantern {
    position: absolute; left: 0; right: 0; top: 150px;
    display: flex; justify-content: center; align-items: center; gap: 14px;
  }
  .brand-lantern .mark { width: 46px; height: 46px; border-radius: 50%; background: var(--blue); }
  .brand-lantern .name { font-size: 64px; font-weight: 600; color: var(--blue); line-height: 1; }
  .headline {
    position: absolute; left: 0; right: 0; top: 288px;
    font-family: "Montserrat", Arial, sans-serif; font-weight: 800;
    font-size: 72px; letter-spacing: 2px; line-height: 1;
    color: var(--heading);
  }
  .intro {
    position: absolute; left: 0; right: 0; top: 375px;
    font-size: 16.5px; line-height: 21px;
  }
  .date-row {
    position: absolute; left: 0; right: 0; top: 446px; height: 105px;
    display: flex; justify-content: center; align-items: center;
  }
  .date-row .month, .date-row .year { font-size: 42px; font-weight: 600; padding: 0 18px; }
  .date-row .day {
    border-left: 1.5px solid var(--ink); border-right: 1.5px solid var(--ink);
    height: 105px; padding: 0 16px; color: var(--red);
    font-size: 40px; font-weight: 600; line-height: 50px;
    display: flex; flex-direction: column; justify-content: center;
  }
  .date-row .day sup { font-size: 22px; }
  .time {
    position: absolute; left: 177px; width: 405px; top: 576px; height: 62px;
    border-top: 1.5px solid var(--red); border-bottom: 1.5px solid var(--red);
    color: var(--red); font-size: 43px; font-weight: 600; line-height: 58px;
  }
  .address { position: absolute; left: 0; right: 0; top: 650px; font-size: 35px; }
  .divider { position: absolute; left: 314px; top: 715px; width: 132px; height: 5px; background: var(--green); }
  .details { position: absolute; left: 0; right: 0; top: 734px; font-size: 21.5px; line-height: 27px; }
  .hospitality { position: absolute; left: 0; right: 0; top: 824px; font-size: 18px; font-style: italic; line-height: 22px; }
  .brand-bloom {
    position: absolute; left: 0; right: 0; top: 864px;
    display: flex; justify-content: center; align-items: center; gap: 8px;
  }
  .brand-bloom .mark { width: 26px; height: 26px; background: var(--blue); }
  .brand-bloom .name { font-size: 20px; font-weight: 600; color: var(--blue); }
  .access { position: absolute; left: 0; right: 0; top: 908px; font-size: 26px; }
  .rsvp {
    position: absolute; left: 230px; width: 300px; top: 950px; height: 23px;
    background: var(--red); color: #fff; font-size: 13px; line-height: 23px;
  }
</style>
</head>
<body>
  <main class="invitation-card">
    <div class="floral-top-right" role="img" aria-label="Watercolour roses and greenery in crimson, lilac and pink"></div>
    <div class="floral-bottom-left" role="img" aria-label="Watercolour lilac roses with green leaves"></div>
    <div class="gold-frame"></div>

    <div class="brand-lantern"><span class="mark"></span><span class="name">Lantern</span></div>

    <h1 class="headline">INVITATION</h1>

    <p class="intro">You’re invited to the official opening and launch of Lantern,<br>Centre of Discovery. An industry first, pioneering, STEM hub.</p>

    <div class="date-row">
      <span class="month">APRIL</span>
      <span class="day"><span>SAT</span><span>30<sup>th</sup></span></span>
      <span class="year">2022</span>
    </div>

    <p class="time">10:00 am – 12:00 pm</p>
    <p class="address">42 Harlow Lane, Fernwood</p>
    <div class="divider"></div>

    <p class="details">All guests will be given a guided walk<br>through of Australia’s first dedicated<br>STEM education hub for children aged 3-6.</p>
    <p class="hospitality">Light canapes provided. Dress code is smart/casual.</p>

    <div class="brand-bloom"><span class="mark"></span><span class="name">Bloom and Grow</span></div>

    <p class="access">Invitation only</p>
    <p class="rsvp">RSVP: 18 April to marketing@bloomandgrow.edu.au</p>
  </main>
</body>
</html>
```